Beilege-Broschüre Online Versand Stuetzwerk.de
Zielgruppe
Bandagen, Orthesen und Sport-Schutzprodukte
Zielgruppe Menschen mit Verletzungen, Sportler und ältere Menschen.
Aufgabenstellung
Vorlage vorhanden und Format bereits festgelegt. Es geht um die kreative Umsetzung der gewünschten Inhalte und Vorbereitung zum druckfähigen Produkt.
Es handelt sich um einen Beileger für Versendungen im Online Bereich. Dieser soll unser Produktportfolio aufzeigen und mit vorhandenem Bildmaterial und Vorlagen erarbeitet werden.
eine INDD Vorlage steht zur Verfügung.

```html
<!DOCTYPE html>
<html lang="de">
<head>
<meta charset="utf-8">
<title>Stuetzwerk.de – Beileger Broschüre</title>
<link href="https://fonts.googleapis.com/css2?family=Open+Sans:wght@400;600&display=swap" rel="stylesheet">
<style>
  :root {
    --paper: #ececec;
    --teal: #0e9bad;
    --teal-dark: #0b7485;
    --navy: #14394d;
    --photo-light: #8a9ca3;
    --photo-dark: #2b3236;
  }
  html, body {
    margin: 0;
    padding: 0;
    width: 1200px;
    height: 730px;
    overflow: hidden;
    background: var(--paper);
  }
  .cover {
    position: relative;
    width: 1200px;
    height: 730px;
    background: var(--paper);
    overflow: hidden;
  }
  .cover__band {
    position: absolute;
    left: 0;
    width: 100%;
    background: var(--teal-dark);
  }
  .cover__band--top { top: 0; height: 16px; }
  .cover__band--bottom { bottom: 0; height: 24px; }
  .cover__shapes {
    position: absolute;
    inset: 16px 0 24px 0;
  }
  .cover__photo {
    position: absolute;
    left: 600px;
    top: 16px;
    width: 560px;
    height: 690px;
  }
  .brand {
    position: absolute;
    left: 80px;
    top: 345px;
    display: flex;
    align-items: center;
    gap: 16px;
  }
  .brand__dot {
    width: 40px;
    height: 40px;
    border-radius: 50%;
    background: var(--navy);
  }
  .brand__name {
    font-family: "Open Sans", sans-serif;
    font-weight: 400;
    font-size: 50px;
    color: var(--navy);
    letter-spacing: 0.5px;
  }
</style>
</head>
<body>
<main class="cover">
  <div class="cover__band cover__band--top"></div>

  <svg class="cover__shapes" width="1200" height="690" viewBox="0 0 1200 690" aria-hidden="true">
    <!-- crescent top -->
    <path d="M500 0 C470 90 490 210 560 270 C560 180 620 80 720 0 Z" fill="var(--teal)"/>
    <!-- large arc behind figure -->
    <circle cx="860" cy="300" r="290" fill="var(--teal)"/>
    <circle cx="1010" cy="360" r="190" fill="var(--paper)"/>
    <!-- top right swoosh -->
    <path d="M1100 0 C1150 60 1180 120 1200 160 L1200 0 Z" fill="var(--teal)"/>
    <!-- lower sweep -->
    <path d="M900 690 C980 620 1100 560 1200 540 L1200 690 Z" fill="var(--teal)"/>
  </svg>

  <svg class="cover__photo" viewBox="0 0 560 690" role="img" aria-label="Sportler mit schwarzer Schulterbandage, schwarz-weiss Foto mit Teal-Einfärbung">
    <defs>
      <linearGradient id="photoTone" x1="0" y1="0" x2="0" y2="1">
        <stop offset="0" stop-color="var(--photo-light)" stop-opacity="0.85"/>
        <stop offset="1" stop-color="var(--photo-dark)" stop-opacity="0.9"/>
      </linearGradient>
    </defs>
    <path d="M170 0 L400 0 L470 160 L520 420 L500 690 L100 690 L80 420 L110 160 Z" fill="url(#photoTone)"/>
  </svg>

  <div class="brand">
    <span class="brand__dot"></span>
    <span class="brand__name">Stuetzwerk.de</span>
  </div>

  <div class="cover__band cover__band--bottom"></div>
</main>
</body>
</html>
```